To design a brand identity that is simple and creative with 'Corvane' as the brand name, I like modern simple fonts like helvetica neue, I want to print both sides of the card, I am open to dark front and white back, but the design needs to transfer well to letter heads and email signatures, I am looking for sophisticated and elegant, but open minded about clever and off the wall, I do not do 'boring' Corvane Ventures is the mother company for a small group, specialising in Management & consulting, Software development and construction, we have a high level of integrity, we are transparent and accountable for what we do. my images are provided as a guide only, Im not expecting them to be just copied, Im looking for a creator and passionate thinker, who will put life into their work.

Target Market(s)

usually business minded people who are looking for something different in me, such as leadership, confidence and focus with thinking that is per haps a little outside the box..

Industry/Entity Type

Construction

Requirements
Must have
• clean, minmalistic
Nice to have
• custom logo
Should not have
• boring, traditional

```html
<!DOCTYPE html>
<html lang="en">
<head>
<meta charset="utf-8">
<title>Corvane Ventures — Business Card</title>
<link rel="stylesheet" href="https://fonts.googleapis.com/css2?family=Montserrat:wght@400;500&display=swap">
<style>
  :root {
    --backdrop: #ececec;
    --card: #f8f8f7;
    --orange: #e0731f;
    --ink: #3b3b3b;
    --muted: #8a8a8a;
  }
  * { margin: 0; padding: 0; box-sizing: border-box; }
  html, body { width: 1200px; height: 952px; overflow: hidden; }
  body {
    background: var(--backdrop);
    font-family: "Montserrat", "Helvetica Neue", Arial, sans-serif;
    position: relative;
  }
  .card {
    position: absolute;
    width: 600px;
    height: 344px;
    background: var(--card);
    box-shadow: 0 2px 6px rgba(0,0,0,.08), 0 14px 30px rgba(0,0,0,.06);
  }
  .card--front { left: 480px; top: 90px; }
  .card--back  { left: 120px; top: 500px; }

  .brand__name {
    font-weight: 500;
    font-size: 54px;
    line-height: 1;
    color: var(--ink);
    letter-spacing: 6px;
    text-transform: uppercase;
  }
  .motto {
    font-size: 13px;
    color: var(--muted);
    letter-spacing: 1px;
  }
  .services {
    font-size: 13px;
    color: var(--ink);
    letter-spacing: .5px;
  }
  .services .sep { color: var(--orange); padding: 0 5px; }

  .card--front .lockup {
    position: absolute; left: 50px; top: 112px; right: 50px;
    text-align: center;
  }
  .card--front .services { margin-top: 18px; }
  .card--front .motto { margin-top: 8px; }

  .contact__email {
    position: absolute; left: 40px; top: 36px;
    font-size: 19px; color: var(--orange); font-weight: 400;
  }
  .contact__role {
    position: absolute; left: 40px; top: 64px;
    font-size: 12px; color: var(--ink);
  }
  .contact__lines {
    position: absolute; left: 40px; top: 220px;
    font-size: 14px; color: var(--ink); line-height: 1.6;
  }
  .contact__lines .label { color: var(--orange); }

  .card--back .lockup {
    position: absolute;
    left: 440px; top: 310px;
    transform: rotate(-90deg);
    transform-origin: left top;
    width: 280px;
  }
  .card--back .brand__name { font-size: 38px; letter-spacing: 4px; }
  .card--back .services { font-size: 11px; margin-top: 10px; }
  .card--back .services .sep { padding: 0 3px; }
  .card--back .motto { font-size: 11px; margin-top: 4px; }
</style>
</head>
<body>
  <section class="card card--front" aria-label="Card front">
    <div class="lockup">
      <p class="brand__name">Corvane</p>
      <p class="services">management<span class="sep">•</span>software<span class="sep">•</span>construction</p>
      <p class="motto">building what comes next</p>
    </div>
  </section>

  <section class="card card--back" aria-label="Card back">
    <p class="contact__email">elliot@corvane.ventures</p>
    <p class="contact__role">client ambassador</p>
    <div class="contact__lines">
      <p><span class="label">M.</span> +61 0400 555 217</p>
      <p><span class="label">PO BOX</span> 418 Perth 6000</p>
    </div>
    <div class="lockup">
      <p class="brand__name">Corvane</p>
      <p class="services">management<span class="sep">•</span>software<span class="sep">•</span>construction</p>
      <p class="motto">building what comes next</p>
    </div>
  </section>
</body>
</html>
```